Vellamoro Wine label**

Hi, we need a design for a white, red and sparkling wine label. We are a small italian restaurant (Vellamoro) and we want to release some wines under our personal brand. The restaurant has a rustic, italian provance style with with a slight modern, clean lines look. We would like a design that represent our mission to provide as authentic Italian food as we can, something that feels that it has been brought from the heart of Italy.
https://www.vellamorobistro.example/

```html
<!DOCTYPE html>
<html lang="it">
<head>
<meta charset="utf-8">
<title>Vellamoro Sangiovese – Wine Label</title>
<link rel="stylesheet" href="https://fonts.googleapis.com/css2?family=Open+Sans:wght@400&display=swap">
<style>
  :root {
    --backdrop: #d9d9d9;
    --label-paper: #f7f7f5;
    --ink: #111111;
    --text-light: #ffffff;
    --tone-indigo: #2a1a5e;
    --tone-blue: #3477b5;
    --tone-rose: #c9687e;
    --tone-amber: #e8a445;
    --tone-crimson: #c8103f;
    --tone-magenta: #d4187a;
  }
  html, body {
    margin: 0;
    padding: 0;
    width: 750px;
    height: 1200px;
    overflow: hidden;
    background: var(--backdrop);
  }
  .canvas {
    position: relative;
    width: 750px;
    height: 1200px;
  }
  .label {
    position: absolute;
    left: 85px;
    top: 50px;
    width: 580px;
    height: 1100px;
    display: flex;
    flex-direction: column;
    box-shadow: 0 6px 24px rgba(0, 0, 0, 0.18);
  }
  .label-header {
    height: 265px;
    background: var(--label-paper);
    display: flex;
    align-items: center;
    justify-content: center;
  }
  .brand-name {
    margin: 0;
    font-family: "Open Sans", sans-serif;
    font-weight: 400;
    font-size: 54px;
    letter-spacing: 0.32em;
    padding-left: 0.32em;
    color: var(--ink);
    text-transform: lowercase;
  }
  .label-body {
    position: relative;
    flex: 1;
  }
  .label-art {
    position: absolute;
    inset: 0;
    width: 100%;
    height: 100%;
    display: block;
  }
  .varietal {
    position: relative;
    margin: 0;
    padding-top: 26px;
    text-align: center;
    font-family: "Open Sans", sans-serif;
    font-weight: 400;
    font-size: 44px;
    letter-spacing: 0.42em;
    padding-left: 0.42em;
    color: var(--text-light);
  }
</style>
</head>
<body>
  <main class="canvas">
    <article class="label">
      <header class="label-header">
        <h1 class="brand-name">Vellamoro</h1>
      </header>
      <section class="label-body">
        <svg class="label-art" viewBox="0 0 580 835" preserveAspectRatio="none"
             role="img" aria-label="Geometric mosaic of overlapping diamonds shading from deep indigo and blue at the top to rose, amber and crimson-magenta at the bottom">
          <defs>
            <linearGradient id="mosaic-tones" x1="0.1" y1="0" x2="0.6" y2="1">
              <stop offset="0" stop-color="var(--tone-indigo)"/>
              <stop offset="0.25" stop-color="var(--tone-blue)"/>
              <stop offset="0.5" stop-color="var(--tone-rose)"/>
              <stop offset="0.72" stop-color="var(--tone-amber)"/>
              <stop offset="0.88" stop-color="var(--tone-crimson)"/>
              <stop offset="1" stop-color="var(--tone-magenta)"/>
            </linearGradient>
          </defs>
          <rect width="580" height="835" fill="url(#mosaic-tones)"/>
        </svg>
        <h2 class="varietal">SANGIOVESE</h2>
      </section>
    </article>
  </main>
</body>
</html>
```